Business Card Design Project - 2 sided

We need a business card design for a card having one business on each side (ie. two businesses on one card). Would like a design that incorporates logo, tagline and normal fields (name, position, address, phone).

Would also like an allowance for small font text along the bottom (text to be determined, but less than 50 characters).

NB. Attached logo for Harbor Quill has two variations - either can be used.

www.harborquill-example.com / www.velmaro-example.com

```html
<!DOCTYPE html>
<html lang="en">
<head>
<meta charset="utf-8">
<title>Harbor Quill / Velmaro – Two-sided Business Card</title>
<link rel="stylesheet" href="https://fonts.googleapis.com/css2?family=Source+Sans+3:wght@400;600;700&display=swap">
<style>
  :root {
    --backdrop: #e8e4df;
    --card: #ffffff;
    --ink: #4a4a4a;
    --ink-soft: #5c5c5c;
    --green: #8cc63f;
    --navy: #2f2b6e;
    --blue: #2b7fba;
    --shadow: rgba(0, 0, 0, 0.22);
  }
  * { margin: 0; padding: 0; box-sizing: border-box; }
  html, body { width: 1200px; height: 487px; overflow: hidden; }
  body {
    background: var(--backdrop);
    font-family: "Source Sans 3", "Myriad Pro", sans-serif;
    color: var(--ink);
    position: relative;
  }
  .card {
    position: absolute;
    top: 90px;
    width: 543px;
    height: 307px;
    background: var(--card);
    border-radius: 18px;
    box-shadow: 0 3px 10px var(--shadow);
  }
  .card--harbor { left: 45px; }
  .card--velmaro { left: 612px; }

  .brand { position: absolute; display: flex; align-items: center; gap: 10px; }
  .brand__dot { width: 34px; height: 34px; border-radius: 50%; background: var(--green); flex: none; }
  .brand__name { font-weight: 600; line-height: 1; }
  .brand__tagline { position: absolute; font-size: 11px; color: var(--ink); white-space: nowrap; }

  .card--harbor .brand { left: 43px; top: 76px; }
  .card--harbor .brand__name { font-size: 26px; color: var(--navy); letter-spacing: 0.5px; }
  .card--harbor .brand__tagline { left: 43px; top: 110px; font-size: 10.5px; font-weight: 600; }

  .card--velmaro .brand { left: 42px; top: 40px; }
  .card--velmaro .brand__dot { width: 44px; height: 44px; }
  .card--velmaro .brand__name { font-size: 42px; color: var(--blue); }
  .card--velmaro .brand__tagline { left: 102px; top: 88px; font-size: 12px; letter-spacing: 0.3px; }

  .person { position: absolute; left: 43px; top: 146px; white-space: nowrap; }
  .card--velmaro .person { left: 40px; top: 141px; }
  .person__name { font-size: 18px; font-weight: 700; color: var(--green); }
  .person__title { font-size: 14px; color: var(--green); }

  .contacts { position: absolute; left: 43px; top: 179px; list-style: none; }
  .card--velmaro .contacts { left: 40px; top: 174px; }
  .contacts li { display: flex; align-items: center; gap: 5px; font-size: 13.5px; line-height: 17.8px; color: var(--ink); }
  .contacts svg { width: 10px; height: 10px; fill: var(--green); flex: none; }

  .address { position: absolute; right: 31px; top: 180px; text-align: right; font-size: 13.5px; line-height: 17.5px; color: var(--ink-soft); }
  .card--velmaro .address { top: 180px; }

  .footnote { position: absolute; left: 41px; top: 272px; font-size: 11px; color: var(--ink-soft); letter-spacing: 0.2px; }
</style>
</head>
<body>

<section class="card card--harbor" aria-label="Harbor Quill side">
  <div class="brand">
    <span class="brand__dot"></span>
    <span class="brand__name">HARBOR QUILL</span>
  </div>
  <p class="brand__tagline">Website Translation and Localisation Specialist...</p>

  <p class="person"><span class="person__name">Your Name</span> <span class="person__title">/ Title</span></p>

  <ul class="contacts">
    <li><svg viewBox="0 0 10 10"><path d="M2 0.5l2 2-1 1.2c.6 1.3 1.6 2.3 2.9 2.9L7 5.6l2 2-1.3 1.9C4.3 9.2.8 5.7.5 2.3z"/></svg>123-456-7890</li>
    <li><svg viewBox="0 0 10 10"><path d="M3 0h4a1 1 0 0 1 1 1v8a1 1 0 0 1-1 1H3a1 1 0 0 1-1-1V1a1 1 0 0 1 1-1zm0 1.5v5h4v-5zm2 6a.8.8 0 1 0 0 1.6.8.8 0 0 0 0-1.6z"/></svg>123-456-7890</li>
    <li><svg viewBox="0 0 10 10"><path d="M0 2.5Q5-.5 10 2.5V4H7.5V3h-5v1H0zM1.5 5h7L10 9.5H0z"/></svg>123-456-7890</li>
    <li><svg viewBox="0 0 10 10"><path d="M0 3l5-2.5L10 3v6.5H0zm1 .6L5 6.3l4-2.7L5 1.6z"/></svg>name@website.com</li>
    <li><svg viewBox="0 0 10 10"><circle cx="5" cy="5" r="4.8"/></svg>www.website.com</li>
  </ul>

  <p class="address">Complex name, Street<br>City, State, zip code</p>

  <p class="footnote">xxxxxxxxxxxxxxxxxxxxxxxxxxxxxxxxxxxxxxxxxxxxxxxxxx</p>
</section>

<section class="card card--velmaro" aria-label="Velmaro side">
  <div class="brand">
    <span class="brand__dot"></span>
    <span class="brand__name">velmaro</span>
  </div>
  <p class="brand__tagline">Professional SEO Services</p>

  <p class="person"><span class="person__name">Your Name</span> <span class="person__title">/ Title</span></p>

  <ul class="contacts">
    <li><svg viewBox="0 0 10 10"><path d="M2 0.5l2 2-1 1.2c.6 1.3 1.6 2.3 2.9 2.9L7 5.6l2 2-1.3 1.9C4.3 9.2.8 5.7.5 2.3z"/></svg>123-456-7890</li>
    <li><svg viewBox="0 0 10 10"><path d="M3 0h4a1 1 0 0 1 1 1v8a1 1 0 0 1-1 1H3a1 1 0 0 1-1-1V1a1 1 0 0 1 1-1zm0 1.5v5h4v-5zm2 6a.8.8 0 1 0 0 1.6.8.8 0 0 0 0-1.6z"/></svg>123-456-7890</li>
    <li><svg viewBox="0 0 10 10"><path d="M0 2.5Q5-.5 10 2.5V4H7.5V3h-5v1H0zM1.5 5h7L10 9.5H0z"/></svg>123-456-7890</li>
    <li><svg viewBox="0 0 10 10"><path d="M0 3l5-2.5L10 3v6.5H0zm1 .6L5 6.3l4-2.7L5 1.6z"/></svg>name@website.com</li>
    <li><svg viewBox="0 0 10 10"><circle cx="5" cy="5" r="4.8"/></svg>www.website.com</li>
  </ul>

  <p class="address">Complex name, Street<br>City, State, zip code</p>

  <p class="footnote">xxxxxxxxxxxxxxxxxxxxxxxxxxxxxxxxxxxxxxxxxxxxxxxxxx</p>
</section>

</body>
</html>
```